Naturopath Practitioner Card Design

I am a naturopath needing a design for a business card mainly to show that I am a naturopath and have some contact details to give to prospective clients. I am open minded about the design and what is on the second side of the card whether it just be some artwork or space for details, appointment times etc. Naturopathy is the practice of natural medicine that uses a holistic approach and incorporates herbal and nutritional medicine.

Industry/Entity Type

Business

Contact Information for Business Card

Tom Rudd NaturopathBHSc (Naturopathy) Member WHPG 0487 925 316 tom.rudd@mailexample.com www.tomruddnaturopathy.example.au

Requirements
Nice to have
• Would prefer some kind of original pattern/art work/logo rather than an image, not fussed if its very simple/basic
• I am open to any colour but think I would prefer a more earthy sandy clay etc type style than the greens that are commonly associated with naturopathy.
Should not have
• Don't really want to have generic stock images on it

```html
<!DOCTYPE html>
<html lang="en">
<head>
<meta charset="utf-8">
<title>Tom Rudd Naturopath – Business Card</title>
<link href="https://fonts.googleapis.com/css2?family=Arimo:wght@400;700&family=Tinos:wght@700&display=swap" rel="stylesheet">
<style>
  :root {
    --stage: #e9e4dc;
    --card-white: #ffffff;
    --ink: #111111;
    --band-black: #050505;
    --accent-green: #2fae2f;
    --dot-line: #222222;
    --shadow: rgba(60, 45, 30, 0.25);
  }
  * { box-sizing: border-box; margin: 0; padding: 0; }
  html, body { width: 1200px; height: 892px; overflow: hidden; }
  body {
    background: var(--stage);
    font-family: "Arimo", Arial, sans-serif;
    color: var(--ink);
    display: flex;
    justify-content: center;
    align-items: center;
    gap: 80px;
  }
  .card {
    position: relative;
    width: 340px;
    height: 556px;
    background: var(--card-white);
    box-shadow: 0 8px 24px var(--shadow);
    overflow: hidden;
  }

  /* Front side */
  .card-front .identity {
    position: absolute;
    top: 34px;
    left: 0;
    right: 0;
    text-align: center;
  }
  .card-front .name {
    font-size: 44px;
    font-weight: 700;
    letter-spacing: 0.5px;
    line-height: 1;
  }
  .card-front .role {
    font-size: 22px;
    margin-top: 4px;
  }
  .card-front .credentials {
    font-size: 17px;
    margin-top: 4px;
  }
  .card-front .herb-art {
    position: absolute;
    top: 170px;
    left: 40px;
    width: 260px;
    height: 170px;
    border-radius: 40% 45% 30% 30%;
    background: radial-gradient(ellipse at 40% 40%, #6f9a4a 0%, #a9c48c 40%, #e8e6dc 70%, #ffffff 100%);
  }
  .card-front .band {
    position: absolute;
    left: 0;
    bottom: 0;
    width: 340px;
    height: 230px;
  }
  .card-front .contact {
    position: absolute;
    left: 0;
    right: 0;
    bottom: 52px;
    text-align: center;
    color: var(--card-white);
  }
  .card-front .phone { font-size: 24px; letter-spacing: 1px; }
  .card-front .email { font-size: 22px; margin-top: 4px; }

  /* Back side */
  .card-back { padding: 46px 30px 0; }
  .card-back .title {
    font-family: "Tinos", "Times New Roman", serif;
    font-weight: 700;
    font-size: 40px;
    text-align: center;
    margin-bottom: 22px;
  }
  .field {
    display: flex;
    align-items: flex-end;
    font-size: 17px;
    font-weight: 700;
    height: 34px;
  }
  .field .label { margin-right: 6px; }
  .field .rule, .blank-line {
    flex: 1;
    border-bottom: 2px dotted var(--dot-line);
    margin-bottom: 4px;
  }
  .days {
    display: grid;
    grid-template-columns: repeat(3, 1fr);
    row-gap: 14px;
    margin-top: 24px;
    font-size: 17px;
  }
  .day { display: flex; align-items: center; gap: 10px; }
  .day .box {
    width: 18px; height: 18px;
    border: 2px solid var(--ink);
  }
  .blank-lines { margin-top: 14px; }
  .blank-line { height: 26px; }
  .card-back .stone-art {
    position: absolute;
    left: 50px;
    bottom: 24px;
    width: 240px;
    height: 150px;
    border-radius: 45% 45% 20% 20%;
    background: radial-gradient(ellipse at 50% 65%, #3a3a3a 0%, #777 28%, #a9cf7d 50%, #eef2e8 75%, #ffffff 100%);
  }
</style>
</head>
<body>
  <section class="card card-front" aria-label="Card front">
    <div class="identity">
      <h1 class="name">Tom Rudd</h1>
      <p class="role">Naturopath</p>
      <p class="credentials">BHSc (Naturopathy) Member WHPG</p>
    </div>
    <div class="herb-art" role="img" aria-label="Photo of fresh herbs, flowers, a white mortar and pestle and herbal capsules"></div>
    <svg class="band" viewBox="0 0 340 230" aria-hidden="true">
      <path d="M0 0 Q170 60 340 150 L340 230 L0 230 Z" fill="var(--band-black)"/>
      <path d="M0 0 Q170 60 340 150" fill="none" stroke="var(--accent-green)" stroke-width="5"/>
    </svg>
    <div class="contact">
      <p class="phone">0487 925 316</p>
      <p class="email">tom.rudd@mailexample.com</p>
    </div>
  </section>

  <section class="card card-back" aria-label="Card back">
    <h2 class="title">Appointment</h2>
    <div class="field"><span class="label">Name:</span><span class="rule"></span></div>
    <div class="field"><span class="label">Date:</span><span class="rule"></span></div>
    <div class="field"><span class="label">Time:</span><span class="rule"></span></div>
    <div class="days">
      <span class="day"><span class="box"></span>MON.</span>
      <span class="day"><span class="box"></span>TUE.</span>
      <span class="day"><span class="box"></span>WED.</span>
      <span class="day"><span class="box"></span>THUR.</span>
      <span class="day"><span class="box"></span>SAT.</span>
      <span class="day"><span class="box"></span>FRI.</span>
    </div>
    <div class="blank-lines">
      <div class="blank-line"></div>
      <div class="blank-line"></div>
      <div class="blank-line"></div>
      <div class="blank-line"></div>
    </div>
    <div class="stone-art" role="img" aria-label="Photo of stacked black spa stones with green bamboo leaves"></div>
  </section>
</body>
</html>
```